About the book: It is an A5 size book, small 40 pages miniguide
Book title: The handy pocket primer on housing loans
Book subtitle: The quick road to riches
Author: Rod Pemberton
Back cover content: Please see attached word document "back page"
Colours: Our company logo should go at the back of the book. One colour we can't use is red. As this is a finance book the red colour is seen negatively. may be light green? you are the expert.
I think lots of white space will work well.
NOTE: please read the back cover notes to get an understanding of what the book is about. It educates readers about finance in property investing. It makes sense that image used combines 'property' and 'finance'. please read back page document attached.
NOTE: it is a small A5 , 40 page book . Its a miniguide rather than a book .

Reason: Dear designers, Thank you for submitting your work over the last few days. Unfortunately we haven't been able to get back to you regarding the final selection of design as the Author of the book has been away on leave with his family without reliable internet access. He is now back and will be giving feedback as we go. We apologise for the time extension. Unfortunately the site didn’t allow me to limit the extension for less than 5 days but we may not require that long. Thanks again. Tova

Reason: We apologies we hadn't finalized a decision on this project due to the person from our end being away. We would like to finalise this design as soon as possible.

Target Market(s)

22 - 45 age group. Most fall between 30-40. Both male and female. couples , individuals etc ...

Industry/Entity Type

Finance

Font styles to use
Other font styles liked:
• sabon/Aeriel. Let me know if any other suggestions.

Requirements
Nice to have
• use green colour if possible but not essential.

```html
<!DOCTYPE html>
<html lang="en">
<head>
<meta charset="utf-8">
<title>The Handy Pocket Primer on Housing Loans – Back Cover</title>
<link href="https://fonts.googleapis.com/css2?family=Arimo:ital,wght@0,400;0,700&display=swap" rel="stylesheet">
<style>
  :root {
    --teal: #3d9ca0;
    --purple: #5a3a78;
    --white: #ffffff;
    --ink: #2b2b2b;
    --logo-dark: #1f4f55;
  }
  * { margin: 0; padding: 0; box-sizing: border-box; }
  html, body { width: 851px; height: 1200px; overflow: hidden; }
  body { font-family: "Arimo", Arial, sans-serif; background: var(--white); }

  .back-cover {
    position: relative;
    width: 851px;
    height: 1200px;
    background: var(--teal);
    color: var(--white);
    overflow: hidden;
  }

  .title-band {
    position: absolute;
    top: 56px;
    left: 0;
    width: 851px;
    height: 100px;
    background: var(--purple);
    text-align: center;
    padding-top: 18px;
  }
  .title-band .book-title {
    font-size: 31px;
    font-weight: 700;
    letter-spacing: 0.5px;
    text-transform: uppercase;
  }
  .title-band .book-subtitle {
    font-size: 22px;
    font-weight: 400;
    margin-top: 8px;
  }

  .blurb {
    position: absolute;
    top: 180px;
    left: 84px;
    width: 690px;
    font-size: 17.5px;
    line-height: 1.42;
  }
  .blurb p { margin-bottom: 0; }
  .lessons {
    list-style: none;
    margin-top: 14px;
  }
  .lessons li {
    position: relative;
    padding-left: 28px;
    margin-bottom: 16px;
  }
  .lessons li::before {
    content: "";
    position: absolute;
    left: 4px;
    top: 8px;
    width: 7px;
    height: 7px;
    border-radius: 50%;
    background: var(--white);
  }
  .lessons strong { font-weight: 700; }

  .brand {
    position: absolute;
    top: 735px;
    left: 220px;
    width: 460px;
  }
  .brand .brand-name {
    display: flex;
    align-items: center;
    gap: 14px;
    font-size: 42px;
    font-weight: 700;
    color: var(--logo-dark);
  }
  .brand .brand-mark {
    width: 36px;
    height: 36px;
    border-radius: 50%;
    background: var(--white);
    flex: none;
  }
  .brand .brand-rule {
    height: 2px;
    background: var(--white);
    margin: 12px 0 10px 0;
  }
  .brand .brand-tagline {
    font-size: 18px;
    color: var(--white);
    padding-left: 4px;
  }

  .contact-bar {
    position: absolute;
    left: 0;
    bottom: 0;
    width: 851px;
    height: 80px;
    background: var(--white);
    display: flex;
    justify-content: space-between;
    align-items: center;
    padding: 0 28px 0 24px;
    color: var(--ink);
  }
  .contact-bar .phone { font-size: 21px; }
  .contact-bar .web { font-size: 24px; font-weight: 700; }
</style>
</head>
<body>
  <div class="back-cover">
    <header class="title-band">
      <h1 class="book-title">The handy pocket primer on housing loans.</h1>
      <p class="book-subtitle">The quick road to riches.</p>
    </header>

    <section class="blurb">
      <p>The number-one reason most investors never own more than one property is finance. For them, getting and managing money is the scariest part of investing.</p>
      <p>You must be 100% informed when structuring your loans. Before you even think about finding a property, you must understand the valuation process.</p>
      <p>In simple, jargon-free language, this mini guide arms you with a wealth of knowledge to reduce risk and keep control of your investment goals.</p>
      <p>Its many vital lessons include:</p>
      <ul class="lessons">
        <li>How to <strong>keep your own home safe</strong> and out of the bank’s hands.</li>
        <li>The first step to successful investing is knowing where you want to finish. Learn how different <strong>exit strategies</strong> affect your investment plan.</li>
        <li>The main reason most Australians aren’t wealthy is that they don’t know the difference between <strong>appreciating and depreciating assets</strong> and <strong>beneficial and non-beneficial liabilities.</strong> Learn to view everything as one or the other.</li>
        <li>Grasping the concept of leverage and other people’s money will dramatically increase your return on equity.</li>
        <li><strong>Banking and finance.</strong> By knowing what lenders need to asses a loan, you can apply with confidence and put yourself ahead of the pack.</li>
      </ul>
    </section>

    <div class="brand">
      <div class="brand-name"><span class="brand-mark"></span>Clearpath Equity</div>
      <div class="brand-rule"></div>
      <p class="brand-tagline">Wealth Building Through Property Investment</p>
    </div>

    <footer class="contact-bar">
      <span class="phone">1300 555 218</span>
      <span class="web">www.clearpathequity.com.au</span>
    </footer>
  </div>
</body>
</html>
```